Interior Design/ New Construction interior finishes

Interior Design Website

Target Market(s)

Home builders, New Construction, Renovations, Public

Industry/Entity Type

Construction

Coding

Coded - Design and coding required

Number of Pages Required

1 page

Font styles to use
Sans Serif

Colors

Designer to choose colors to be used in the design.

Requirements
Must have
• Section to upload pictures of projects
• Simple and modern design
• Designer 1 details about myself
• Logo
• Upload section for photos for future jobs
Nice to have
• Sections they can click on to see certain rooms in a house
• Decorating, floral arrangements, holiday decorating.
• I have lots of before and after as well. Maybe a section for those.

```html
<!DOCTYPE html>
<html lang="en">
<head>
<meta charset="utf-8">
<title>Linden Interiors – Interior Business &amp; New Construction</title>
<link rel="stylesheet" href="https://fonts.googleapis.com/css2?family=Playfair+Display:ital,wght@0,400;1,400&family=Montserrat:wght@500;600&display=swap">
<style>
  :root {
    --linen: #e8e8e7;
    --white: #ffffff;
    --ink: #1a1a1a;
    --panel: rgba(12, 12, 12, 0.9);
    --muted: #6d6d6d;
    --rule: #d6d6d6;
    --serif: 'Playfair Display', Georgia, serif;
    --sans: 'Montserrat', Arial, sans-serif;
  }
  * { box-sizing: border-box; margin: 0; padding: 0; }
  html, body { width: 1200px; height: 2302px; overflow: hidden; }
  body { background: var(--linen); color: var(--ink); font-family: var(--serif); position: relative; }

  .brand { position: absolute; left: 0; width: 1200px; text-align: center; }
  .brand-mark { display: block; margin: 0 auto; border: 2px solid var(--ink); border-radius: 50%; }
  .brand-name { display: block; font-family: var(--sans); font-weight: 500; letter-spacing: 2px; color: var(--ink); }
  .site-header .brand { top: 26px; }
  .site-header .brand-mark { width: 62px; height: 62px; }
  .site-header .brand-name { font-size: 19px; margin-top: 8px; }

  .menu-toggle { position: absolute; top: 72px; left: 1048px; display: flex; align-items: center; gap: 14px;
    font-family: var(--sans); font-weight: 600; font-size: 15px; color: var(--ink); }
  .menu-toggle svg { display: block; }

  .hero { position: absolute; left: 54px; top: 141px; width: 1097px; height: 651px;
    background: linear-gradient(160deg, #7a6a63 0%, #8f7c6c 35%, #6e5546 65%, #4d3a2e 100%); }
  .hero-title { position: absolute; top: 240px; width: 100%; text-align: center; color: var(--white);
    font-weight: 400; font-size: 58px; line-height: 59px; }
  .btn-outline { display: inline-flex; align-items: center; justify-content: center; border: 3px solid var(--white);
    border-radius: 30px; color: var(--white); font-family: var(--sans); font-weight: 500; text-transform: uppercase; }
  .hero .btn-outline { position: absolute; left: 450px; top: 387px; width: 192px; height: 47px; font-size: 13px; }
  .slider-dots { position: absolute; top: 610px; left: 516px; display: flex; gap: 11px; }
  .slider-dots span { width: 7px; height: 7px; border-radius: 50%; background: rgba(255,255,255,0.55); }
  .slider-dots span:first-child { background: var(--white); }

  .service { position: absolute; overflow: hidden; }
  .service-photo { position: absolute; inset: 0; }
  .service--decorating { left: 54px; top: 826px; width: 532px; height: 744px; }
  .service--decorating .service-photo { background: linear-gradient(170deg, #f1f1ef 0%, #d9d6d1 40%, #7c6a5a 75%, #3d3028 100%); }
  .service--holiday { left: 612px; top: 826px; width: 539px; height: 357px; }
  .service--holiday .service-photo { background: linear-gradient(100deg, #3a3835 0%, #8d8a86 50%, #d9d7d3 80%, #5b6b4a 100%); }
  .service--floral { left: 612px; top: 1212px; width: 539px; height: 358px; }
  .service--floral .service-photo { background: linear-gradient(180deg, #f2f0ec 0%, #dcd6cc 55%, #9aa3ad 100%); }

  .service-card { position: absolute; }
  .service-frame { position: absolute; inset: 0; width: 100%; height: 100%; }
  .service-panel { position: absolute; inset: 20px; background: var(--panel); display: flex; flex-direction: column;
    align-items: center; justify-content: center; color: var(--white); text-align: center; }
  .service-panel h2 { font-weight: 400; font-size: 35px; line-height: 37px; }
  .service-panel .btn-outline { width: 138px; height: 34px; font-size: 12px; margin-top: 17px; }
  .service--decorating .service-card { left: 95px; top: 173px; width: 357px; height: 351px; }
  .service--decorating .service-panel h2 { margin-top: 100px; }
  .service--holiday .service-card, .service--floral .service-card { left: 91px; top: 29px; width: 357px; height: 301px; }
  .service--holiday .service-panel h2, .service--floral .service-panel h2 { margin-top: 20px; }

  .before-after { position: absolute; left: 0; top: 1631px; width: 1200px; height: 411px; background: var(--white); }
  .before-after h2 { position: absolute; top: 30px; width: 100%; text-align: center; font-weight: 400; font-size: 58px; }
  .ba-arrow { position: absolute; top: 140px; }
  .ba-arrow--prev { left: 29px; }
  .ba-arrow--next { left: 1155px; }
  .ba-divider { position: absolute; left: 601px; top: 116px; width: 1px; height: 245px; background: var(--rule); }
  .ba-item { position: absolute; top: 129px; width: 246px; }
  .ba-photo { position: relative; height: 170px; }
  .ba-photo span { position: absolute; left: 20px; bottom: 14px; color: var(--white); font-size: 19px; }
  .ba-item p { margin-top: 15px; font-style: italic; font-size: 12px; line-height: 18px; color: var(--muted); text-align: center; padding: 0 6px; }
  .ba-photo--room-before { background: linear-gradient(180deg, #d8d4cf 0%, #c2bcb4 70%, #4a3f37 100%); }
  .ba-photo--room-after { background: linear-gradient(180deg, #7a241c 0%, #8e3a2b 60%, #2f241e 100%); }
  .ba-photo--door-before { background: linear-gradient(90deg, #3a3a3a 0%, #9a9c95 50%, #7b2b22 100%); }
  .ba-photo--door-after { background: linear-gradient(90deg, #e3e3e1 0%, #2b2d2c 40%, #6e8f4e 70%, #2b2d2c 100%); }

  .site-footer .brand { top: 2072px; }
  .site-footer .brand-mark { width: 44px; height: 44px; }
  .site-footer .brand-name { font-size: 14px; margin-top: 6px; }
  .newsletter { position: absolute; top: 2170px; left: 268px; display: flex; align-items: center; }
  .newsletter label { font-size: 18px; width: 195px; }
  .newsletter-field { width: 468px; height: 61px; border: 1px solid #9a9a9a; border-radius: 8px; background: var(--white);
    display: flex; align-items: center; justify-content: space-between; padding: 0 8px 0 17px; }
  .newsletter-field span { font-size: 12px; color: var(--muted); }
  .newsletter-field button { width: 155px; height: 45px; border: 0; border-radius: 8px; background: #000; color: var(--white);
    font-family: var(--serif); font-size: 15px; }
  .copyright { position: absolute; top: 2255px; width: 1200px; text-align: center; font-size: 12px; }
</style>
</head>
<body>
  <header class="site-header">
    <div class="brand">
      <span class="brand-mark"></span>
      <span class="brand-name">Linden Interiors</span>
    </div>
    <div class="menu-toggle">Menu
      <svg width="27" height="22" viewBox="0 0 27 22" aria-hidden="true">
        <path d="M1 2h25M7 8h19M1 14h25M7 20h19" stroke="#1a1a1a" stroke-width="1.5"/>
      </svg>
    </div>
  </header>

  <section class="hero" role="img" aria-label="Open-plan dining room and kitchen with round wooden table and wrought-iron staircase">
    <h1 class="hero-title">Interior Business &amp;<br>New Construction Company</h1>
    <span class="btn-outline">Learn More</span>
    <div class="slider-dots"><span></span><span></span><span></span><span></span></div>
  </section>

  <article class="service service--decorating">
    <div class="service-photo" role="img" aria-label="Dining room with candle chandelier, grey upholstered chair and rustic wooden bench"></div>
    <div class="service-card">
      <svg class="service-frame" viewBox="0 0 100 100" preserveAspectRatio="none" aria-hidden="true">
        <path d="M4 0H96A4 4 0 0 0 100 4V96A4 4 0 0 0 96 100H4A4 4 0 0 0 0 96V4A4 4 0 0 0 4 0Z" fill="none" stroke="#fff" stroke-width="2" vector-effect="non-scaling-stroke"/>
      </svg>
      <div class="service-panel"><h2>Decorating</h2><span class="btn-outline">Read More</span></div>
    </div>
  </article>

  <article class="service service--holiday">
    <div class="service-photo" role="img" aria-label="Living room with lanterns, fireplace and decorated Christmas tree"></div>
    <div class="service-card">
      <svg class="service-frame" viewBox="0 0 100 100" preserveAspectRatio="none" aria-hidden="true">
        <path d="M4 0H96A4 4 0 0 0 100 4V96A4 4 0 0 0 96 100H4A4 4 0 0 0 0 96V4A4 4 0 0 0 4 0Z" fill="none" stroke="#fff" stroke-width="2" vector-effect="non-scaling-stroke"/>
      </svg>
      <div class="service-panel"><h2>Holiday<br>Decorating</h2><span class="btn-outline">Read More</span></div>
    </div>
  </article>

  <article class="service service--floral">
    <div class="service-photo" role="img" aria-label="Bright sitting room with white tufted sofas and a blue patterned rug"></div>
    <div class="service-card">
      <svg class="service-frame" viewBox="0 0 100 100" preserveAspectRatio="none" aria-hidden="true">
        <path d="M4 0H96A4 4 0 0 0 100 4V96A4 4 0 0 0 96 100H4A4 4 0 0 0 0 96V4A4 4 0 0 0 4 0Z" fill="none" stroke="#fff" stroke-width="2" vector-effect="non-scaling-stroke"/>
      </svg>
      <div class="service-panel"><h2>Floral<br>Arrangements</h2><span class="btn-outline">Read More</span></div>
    </div>
  </article>

  <section class="before-after">
    <h2>Before &amp; After</h2>
    <svg class="ba-arrow ba-arrow--prev" width="14" height="22" viewBox="0 0 14 22" aria-hidden="true"><path d="M11 3L4 11l7 8" fill="none" stroke="#000" stroke-width="3"/></svg>
    <svg class="ba-arrow ba-arrow--next" width="14" height="22" viewBox="0 0 14 22" aria-hidden="true"><path d="M3 3l7 8-7 8" fill="none" stroke="#000" stroke-width="3"/></svg>
    <div class="ba-divider"></div>

    <figure class="ba-item" style="left:67px">
      <div class="ba-photo ba-photo--room-before" role="img" aria-label="Empty beige room with window before renovation"><span>Before</span></div>
      <p>Inventore veritatis et quasi architecto beatae vitae dicta sunt explicabo.</p>
    </figure>
    <figure class="ba-item" style="left:319px">
      <div class="ba-photo ba-photo--room-after" role="img" aria-label="Same room painted red and furnished as a dining room"><span>After</span></div>
      <p>Inventore veritatis et quasi architecto beatae vitae dicta sunt explicabo.</p>
    </figure>
    <figure class="ba-item" style="left:635px">
      <div class="ba-photo ba-photo--door-before" role="img" aria-label="Unfinished wall opening for patio doors before renovation"><span>Before</span></div>
      <p>Inventore veritatis et quasi architecto beatae vitae dicta sunt explicabo.</p>
    </figure>
    <figure class="ba-item" style="left:885px">
      <div class="ba-photo ba-photo--door-after" role="img" aria-label="Finished room with black-framed sliding glass doors onto a garden"><span>After</span></div>
      <p>Inventore veritatis et quasi architecto beatae vitae dicta sunt explicabo.</p>
    </figure>
  </section>

  <footer class="site-footer">
    <div class="brand">
      <span class="brand-mark"></span>
      <span class="brand-name">Linden Interiors</span>
    </div>
    <form class="newsletter">
      <label>Join Our Mailing List</label>
      <div class="newsletter-field">
        <span>Enter Your E-Mail address</span>
        <button type="button">Subscribe Now</button>
      </div>
    </form>
    <p class="copyright">© 2018 Company Name | All Rights Reserved</p>
  </footer>
</body>
</html>
```